4D Cradle Glimpse Luxury Ultrasound Billboard

Design a HIGH-END, MODERN billboard for my private prenatal ultrasound studio, 4D Cradle Glimpse, located in Pace, Florida.
This billboard will be viewed by drivers traveling at highway speeds, so it must be extremely clean, simple, and readable within 6 seconds.
About My Business
4D Cradle Glimpse is a private prenatal ultrasound studio specializing in:
Highest technology 4D/HD Ultrasounds
Early Gender Determination
Pregnancy Confirmation
I have been serving families for nearly 10 years and is known for creating a memorable experience, not just an ultrasound appointment.
Design Style
I DO NOT want:
Flowers
Leaves
Swirls
Glitter
Hearts everywhere
Busy backgrounds
Generic maternity stock graphics
I DO want:
Modern
Luxury
Upscale
Clean
Professional
Eye-catching
Premium medical spa feel
Colors
Use colors from my logo:
LOGO Green ( or a deep green)
Black
White
Soft Gold accents
Images:
Incorporate my professional headshot in a clean, modern way, logo, and the ultrasound images
Text
Keep wording minimal.
Primary Headline ( OPEN TO IDEAS) :
EXAMPLES ( WOULD RATHER SOMETHING MORE CATCHY)
" ADVANCED IMAGING. UNFORGETTABLE MOMENTS"
"MEET YOUR BABY BEFORE BIRTH"
Under headline:
4D Ultrasound • Early Gender • Pregnancy Confirmation
Business Name:
4D Cradle Glimpse
Private Prenatal Ultrasound Studio
Phone Number:
850-471-5923
Important
This billboard must be readable in 5–6 seconds from a moving vehicle.
Less text is better.
The phone number and business name must be visible from a distance.
The design should feel like a premium brand that immediately tells expecting parents:
“This is where I go to see my baby.”
Files Provided
Official logo
Headshot
Ultrasound images
Don’t make this look like a medical office billboard.
Make it look like a luxury baby experience billboard. That’s what separates 4D Cradle Glimpse from hospitals, OB offices, and all the new studios popping up around you. The emotional connection is what gets moms to book. ❤️
Billboard Size - 10.6” x 36”

```html
<!DOCTYPE html>
<html lang="en">
<head>
<meta charset="utf-8">
<title>4D Cradle Glimpse Billboard</title>
<link rel="stylesheet" href="https://fonts.googleapis.com/css2?family=Libre+Baskerville:wght@400;700&family=Montserrat:wght@600;800&display=swap">
<style>
  :root {
    --sage: #5f6e67;
    --sage-deep: #4c5a53;
    --gold: #e0ac36;
    --white: #ffffff;
    --ink: #55605b;
    --stage: #c8c8c8;
  }
  * { margin: 0; padding: 0; box-sizing: border-box; }
  html, body { width: 1200px; height: 1160px; overflow: hidden; background: var(--stage); }
  .billboard {
    position: absolute; left: 40px; top: 415px;
    width: 1120px; height: 330px;
    background: var(--white); overflow: hidden;
  }
  .billboard__panels { position: absolute; inset: 0; }
  .brand-box {
    position: absolute; left: 35px; top: 29px; width: 458px; height: 221px;
    background: var(--white); border: 4px solid var(--sage); border-radius: 32px;
    box-shadow: 0 0 0 5px var(--white);
    display: flex; flex-direction: column; align-items: center; justify-content: center;
    color: var(--sage); text-align: center;
  }
  .brand-box__name {
    font-family: "Libre Baskerville", serif; font-weight: 700; color: var(--sage);
    line-height: 1.05;
  }
  .brand-box__name .lead { display: block; font-size: 56px; }
  .brand-box__name .rest { display: block; font-size: 40px; }
  .brand-box__rule { width: 400px; height: 2px; background: var(--gold); margin: 14px 0 12px; }
  .brand-box__tagline {
    font-family: "Montserrat", sans-serif; font-weight: 600; font-size: 15px;
    letter-spacing: 1.5px; color: var(--ink); text-transform: uppercase;
  }
  .phone {
    position: absolute; left: 28px; top: 258px; height: 66px;
    display: flex; align-items: center; gap: 8px;
    font-family: "Montserrat", sans-serif; font-weight: 800; font-size: 52px;
    color: var(--white); letter-spacing: 0.5px;
  }
  .phone svg { width: 38px; height: 38px; }
  .headshot {
    position: absolute; left: 515px; top: 26px; width: 218px; height: 304px;
    background: linear-gradient(180deg, #d9c79a 0%, #e6c8ad 35%, #3f5a3c 70%, #f1efea 100%);
    border-radius: 100px 100px 0 0;
  }
  .scan {
    position: absolute; left: 682px; top: 219px; width: 104px; height: 104px;
    border-radius: 50%; border: 4px solid var(--white);
    box-shadow: 0 0 0 2px var(--sage);
    background: radial-gradient(circle at 40% 45%, #b77a68 0%, #8a4c3e 55%, #3a1e18 100%);
  }
  .headline {
    position: absolute; left: 752px; top: 14px; width: 350px;
    font-family: "Libre Baskerville", serif; text-align: center; line-height: 1;
  }
  .headline__intro { display: block; font-size: 37px; font-weight: 400; color: var(--white); }
  .headline__accent { display: block; font-size: 66px; font-weight: 700; color: var(--gold); margin-top: 8px; }
  .headline__close { display: block; font-size: 74px; font-weight: 700; color: var(--white); margin-top: 2px; }
  .services {
    position: absolute; left: 797px; top: 260px;
    font-family: "Libre Baskerville", serif; font-size: 18px; color: var(--ink);
    line-height: 1.45; list-style: none;
  }
</style>
</head>
<body>
  <div class="billboard">
    <svg class="billboard__panels" width="1120" height="330" viewBox="0 0 1120 330" aria-hidden="true">
      <path d="M433 0 H1120 V234 H733 V330 H0 V234 H403 V30 Q403 0 433 0 Z" fill="var(--sage)"/>
      <line x1="733" y1="237" x2="1120" y2="237" stroke="var(--sage)" stroke-width="2"/>
    </svg>

    <div class="brand-box">
      <p class="brand-box__name"><span class="lead">4D</span><span class="rest">Cradle Glimpse</span></p>
      <div class="brand-box__rule"></div>
      <p class="brand-box__tagline">Prenatal Ultrasound Studio</p>
    </div>

    <p class="phone">
      <svg viewBox="0 0 24 24" aria-hidden="true"><path fill="#fff" d="M6.6 10.8a15.2 15.2 0 0 0 6.6 6.6l2.2-2.2a1 1 0 0 1 1-.25 11.4 11.4 0 0 0 3.6.57 1 1 0 0 1 1 1V20a1 1 0 0 1-1 1A17 17 0 0 1 3 4a1 1 0 0 1 1-1h3.5a1 1 0 0 1 1 1c0 1.25.2 2.45.57 3.57a1 1 0 0 1-.25 1Z"/></svg>
      850-471-5923
    </p>

    <div class="headshot" role="img" aria-label="Portrait of the studio owner in green scrubs holding an ultrasound probe"></div>
    <div class="scan" role="img" aria-label="4D ultrasound image of twin babies"></div>

    <h1 class="headline">
      <span class="headline__intro">Meet Your Baby</span>
      <span class="headline__accent">BEFORE</span>
      <span class="headline__close">BIRTH</span>
    </h1>

    <ul class="services">
      <li>• 4D Ultrasound • Early Gender</li>
      <li>• Pregnancy Confirmation</li>
    </ul>
  </div>
</body>
</html>
```